Business Card for beauty technology startup

Design Glimora Business Card for a Beauty, based on the website identity and colors (https://www.glimora-example.com).
Glimora is a beauty tech startup that gathers helpful product info for beauty lovers and consumers (such as availability on stores, price range and product reviews) for makeup products. The card design must be young, colorful but clean, and very modern.

Target Market(s)

woman, 15-35

Industry/Entity Type

Cosmetics

Contact Information for Business Card

Full Name, address, phone

Font styles to use
Other font styles liked:
• Advent Pro

Colors
e34297
86cfc6
ffffff
5c5c5c
e8e8e8
e667a6
b2b2b2

Requirements
Must have
• One full colored side with a creative design and another with card info
• Use Color palette: #95C5C5 and/or #D38AA5
• Use fonts: Advent Pro
• Use website identity: https://www.glimora-example.com
Nice to have
• If needed extra font: Roboto

```html
<!DOCTYPE html>
<html lang="en">
<head>
<meta charset="utf-8">
<title>Glimora Business Card</title>
<link rel="stylesheet" href="https://fonts.googleapis.com/css2?family=Advent+Pro:wght@300;400&family=Roboto:wght@400;500;700&display=swap">
<style>
  :root {
    --page-bg: #e6e6e6;
    --card-white: #f6f6f6;
    --rose: #b97b92;
    --rose-back: #bb7c91;
    --rose-light: #eaa6c0;
    --accent-grey: #8d8d8d;
    --text-grey: #555555;
  }
  * { margin: 0; padding: 0; box-sizing: border-box; }
  html, body { width: 1200px; height: 960px; overflow: hidden; }
  body { background: var(--page-bg); position: relative; font-family: "Roboto", sans-serif; }

  .card {
    position: absolute;
    width: 600px;
    height: 343px;
    border-radius: 20px;
    overflow: hidden;
    box-shadow: 0 3px 6px rgba(0,0,0,0.25);
  }
  .card-front { left: 314px; top: 113px; background: var(--card-white); }
  .card-back { left: 312px; top: 473px; background: var(--rose-back); }

  .corner-accents { position: absolute; inset: 0; width: 100%; height: 100%; }

  .brand-block {
    position: absolute;
    left: 78px;
    top: 88px;
    width: 200px;
    text-align: center;
  }
  .brand-dot {
    width: 100px;
    height: 100px;
    border: 3px solid var(--rose);
    border-radius: 50%;
    margin: 0 auto 38px;
  }
  .brand-name {
    font-family: "Advent Pro", sans-serif;
    font-weight: 300;
    font-size: 46px;
    letter-spacing: 4px;
    color: var(--rose);
    line-height: 1;
  }

  .divider {
    position: absolute;
    left: 309px;
    top: 60px;
    width: 2px;
    height: 232px;
    background: linear-gradient(to bottom, transparent, #d0d0d0 20%, #d0d0d0 80%, transparent);
  }

  .contact-block { position: absolute; left: 346px; top: 72px; color: var(--text-grey); }
  .person-name { font-weight: 700; font-size: 19px; color: var(--rose); line-height: 22px; }
  .person-title { font-weight: 500; font-size: 15px; line-height: 20px; }
  .address { font-size: 14px; line-height: 19px; margin-top: 10px; }
  .contact-list { list-style: none; margin-top: 10px; font-size: 14px; }
  .contact-list li { display: flex; align-items: center; height: 19px; }
  .contact-list svg { width: 14px; height: 14px; margin-right: 9px; fill: var(--rose); }

  .back-name {
    position: absolute;
    right: 32px;
    top: 242px;
    font-family: "Advent Pro", sans-serif;
    font-weight: 300;
    font-size: 50px;
    letter-spacing: 4px;
    color: var(--rose-light);
    line-height: 1;
    text-align: right;
  }
  .back-url {
    position: absolute;
    right: 32px;
    top: 300px;
    font-family: "Advent Pro", sans-serif;
    font-weight: 400;
    font-size: 13px;
    letter-spacing: 3px;
    color: var(--rose-light);
  }
</style>
</head>
<body>

<section class="card card-front">
  <svg class="corner-accents" viewBox="0 0 600 343" aria-hidden="true">
    <path d="M0 0 H100 Q30 25 0 80 Z" fill="var(--accent-grey)"/>
    <path d="M0 0 H80 Q20 25 0 70 Z" fill="var(--rose)"/>
    <path d="M600 343 H460 Q570 330 600 262 Z" fill="var(--accent-grey)"/>
    <path d="M600 343 H510 Q580 320 600 275 Z" fill="var(--rose)"/>
  </svg>

  <div class="brand-block">
    <div class="brand-dot"></div>
    <div class="brand-name">GLIMORA</div>
  </div>

  <div class="divider"></div>

  <div class="contact-block">
    <div class="person-name">LENA MARWOOD</div>
    <div class="person-title">CEO/FOUNDER</div>
    <div class="address">1420 Orchid Row<br>Fairbrook, Oregon 50812</div>
    <ul class="contact-list">
      <li><svg viewBox="0 0 16 16"><path d="M3 1l3 3-1.5 2a9 9 0 0 0 5.5 5.5L12 10l3 3-2 2C7 15 1 9 1 3z"/></svg>555 214 7730</li>
      <li><svg viewBox="0 0 16 16"><path d="M4 0h8v16H4z M5.5 2v10h5V2z"/></svg>555 389 1046</li>
      <li><svg viewBox="0 0 16 16"><path d="M4 1h8v4H4z M1 6h14v7h-3v2H4v-2H1z M5 11v3h6v-3z"/></svg>555 602 8815</li>
      <li><svg viewBox="0 0 16 16"><path d="M1 4h14v9H1z M1.5 4.5 8 9l6.5-4.5" stroke="#fff" stroke-width="1"/></svg>info@glimora-example.com</li>
      <li><svg viewBox="0 0 16 16"><circle cx="8" cy="8" r="7"/></svg>www.glimora-example.com</li>
    </ul>
  </div>
</section>

<section class="card card-back">
  <div class="back-name">GLIMORA</div>
  <div class="back-url">www.glimora-example.com</div>
</section>

</body>
</html>
```